Corporate Business Card

Very professional, Modern, Not to busy, include phone address email, website
(253) 617-4930, 18761 52nd Avenue S, Kent, WA 98047, martin@plumlinegroup.com, varkoworks.com

Target Market(s)

Manufacturing

Industry/Entity Type

Aero, machining, manufacturing, Off road racing

Contact Information for Business Card

Phone, address email, website

```html
<!DOCTYPE html>
<html lang="en">
<head>
<meta charset="utf-8">
<title>Varko Works – Business Card</title>
<link rel="stylesheet" href="https://fonts.googleapis.com/css2?family=Montserrat:wght@400;500;700&display=swap">
<style>
  :root {
    --navy: #17366f;
    --red: #d3222a;
    --white: #ffffff;
    --backdrop: #4a4a4a;
    --ink-soft: rgba(255,255,255,0.09);
  }
  * { box-sizing: border-box; margin: 0; padding: 0; }
  html, body { width: 1200px; height: 801px; overflow: hidden; }
  body {
    background: var(--backdrop);
    font-family: "Montserrat", Arial, sans-serif;
    color: var(--white);
    position: relative;
  }
  .card {
    position: absolute;
    top: 245px;
    width: 540px;
    height: 310px;
    background: var(--navy);
    overflow: hidden;
  }
  .card--front { left: 40px; }
  .card--back { left: 620px; }

  .brand {
    position: absolute;
    display: flex;
    align-items: center;
    gap: 10px;
    font-weight: 700;
    color: var(--white);
    letter-spacing: 0.5px;
    white-space: nowrap;
  }
  .brand__mark { background: var(--red); flex: none; }
  .card--front .brand { left: 32px; top: 34px; font-size: 30px; }
  .card--front .brand__mark { width: 14px; height: 14px; }
  .card--back .brand { left: 50%; top: 50%; transform: translate(-50%, -50%); font-size: 50px; }
  .card--back .brand__mark { width: 22px; height: 22px; }

  .brand-faint {
    position: absolute;
    left: 250px; top: 140px;
    font-size: 36px;
    font-weight: 700;
    color: var(--ink-soft);
    white-space: nowrap;
  }

  .holder { position: absolute; right: 32px; top: 34px; text-align: right; }
  .holder__name { color: var(--red); font-weight: 700; font-size: 17px; letter-spacing: 0.8px; }
  .holder__title { font-size: 11px; font-weight: 400; margin-top: 4px; letter-spacing: 0.3px; }

  .address { position: absolute; left: 32px; top: 136px; font-size: 11.5px; line-height: 1.55; letter-spacing: 0.3px; }

  .contacts { position: absolute; left: 32px; top: 196px; list-style: none; font-size: 11.5px; letter-spacing: 0.3px; }
  .contacts li { display: flex; align-items: center; gap: 8px; line-height: 1; margin-bottom: 7px; }
  .contacts svg { width: 11px; height: 11px; flex: none; }

  .edge-tab { position: absolute; right: 0; top: 0; width: 10px; height: 42px; background: var(--red); }
  .base-band { position: absolute; left: 0; right: 0; bottom: 0; height: 14px; display: flex; gap: 6px; }
  .base-band__red { background: var(--red); flex: 0 0 50%; }
  .base-band__white { background: var(--white); flex: 1; }
</style>
</head>
<body>
  <section class="card card--front" aria-label="Business card front">
    <div class="brand"><span class="brand__mark"></span>Varko Works</div>
    <div class="brand-faint" aria-hidden="true">Varko Works</div>
    <div class="holder">
      <p class="holder__name">DANIEL REYES</p>
      <p class="holder__title">Owner/CEO</p>
    </div>
    <p class="address">4130, 18761 52nd Avenue<br>S, Kent, WA 98047</p>
    <ul class="contacts">
      <li>
        <svg viewBox="0 0 24 24" aria-hidden="true"><path fill="#d3222a" d="M6.6 10.8a15.1 15.1 0 0 0 6.6 6.6l2.2-2.2a1 1 0 0 1 1-.25 11.4 11.4 0 0 0 3.6.57 1 1 0 0 1 1 1V20a1 1 0 0 1-1 1A17 17 0 0 1 3 4a1 1 0 0 1 1-1h3.5a1 1 0 0 1 1 1c0 1.25.2 2.45.57 3.57a1 1 0 0 1-.25 1z"/></svg>
        (253) 617-4930
      </li>
      <li>
        <svg viewBox="0 0 24 24" aria-hidden="true"><path fill="#d3222a" d="M2 5h20v14H2zm2 2v.5l8 5 8-5V7l-8 5z"/></svg>
        martin@plumlinegroup.com
      </li>
      <li>
        <svg viewBox="0 0 24 24" aria-hidden="true"><circle cx="12" cy="12" r="9" fill="none" stroke="#d3222a" stroke-width="2.4"/><path d="M3 12h18M12 3c3 3.5 3 14.5 0 18M12 3c-3 3.5-3 14.5 0 18" fill="none" stroke="#d3222a" stroke-width="1.8"/></svg>
        www.varkoworks.com
      </li>
    </ul>
    <div class="edge-tab"></div>
    <div class="base-band"><span class="base-band__red"></span><span class="base-band__white"></span></div>
  </section>

  <section class="card card--back" aria-label="Business card back">
    <div class="brand"><span class="brand__mark"></span>Varko Works</div>
  </section>
</body>
</html>
```